4th Generation Family Business Needs a New Card Design!

We are a family owned 4th Generation company. We are based in the Sydney, Australia area and we are desperately in need of a more modern and classy card. We are monumental masons who design, supply & erect lasting memorials throughout cemeteries in Sydney. Our customers are normally in a period of grieving. I have attached logo files that will need to be implemented on the card. Company was established 1935. Australian Owned and Operated. Card needs to be designed to PIXO.com specification.

Target Market(s)

Our target market is based upon people that a grieving for family members that have passed away. We also deal with alot of companies that own and operate cemeteries.

Industry/Entity Type

Business

Contact Information for Business Card

Simon Harcourt, Operations Manager, 0417293086, simon@harcourtmemorials.com.au
Lewis Harcourt, Director, 0491630572, lewis@harcourtmemorials.com.au
Phone # 02 9561 3048
Website: www.harcourtmemorials.com.au
Address: Suite 17, 8 Palfrey Lane, West Carlow, Sydney NSW 2156

Font styles to use
Serif
Decorative
Script

Requirements
Must have
• Would like to see the logo nicely implemented with a modern design. Embossed lettering would be a nice additive.

```html
<!DOCTYPE html>
<html lang="en">
<head>
<meta charset="utf-8">
<title>Harcourt Memorials – Business Card</title>
<link rel="stylesheet" href="https://fonts.googleapis.com/css2?family=Cinzel:wght@500;700&family=Libre+Baskerville:wght@400&display=swap">
<style>
  :root {
    --backdrop: #e9e7e4;
    --card-black: #141414;
    --card-black-raised: #2a2a2a;
    --card-white: #f8f8f6;
    --ink: #1a1a1a;
    --ink-soft: #3a3a3a;
    --gold: #e2ae1e;
    --stripe: #121212;
  }
  * { margin: 0; padding: 0; box-sizing: border-box; }
  html, body {
    width: 1200px; height: 716px; overflow: hidden;
    background: var(--backdrop);
  }
  .canvas {
    position: relative; width: 1200px; height: 716px;
    display: flex; align-items: center; justify-content: center; gap: 48px;
  }
  .card {
    position: relative; width: 500px; height: 286px;
    box-shadow: 0 6px 18px rgba(0,0,0,0.18);
    overflow: hidden;
  }

  /* Back */
  .card-back {
    background: var(--card-black);
    display: flex; align-items: center; justify-content: center; gap: 14px;
  }
  .card-back .brand-mark {
    width: 22px; height: 22px; background: var(--card-black-raised);
  }
  .card-back .brand-name {
    font-family: "Cinzel", serif; font-weight: 700; font-size: 30px;
    letter-spacing: 2px; color: var(--card-black-raised);
  }

  /* Front */
  .card-front { background: var(--card-white); }
  .card-front .stripe {
    position: absolute; left: 0; top: 0; bottom: 0; width: 44px;
    background: var(--stripe);
  }
  .card-front .gold-rule {
    position: absolute; left: 52px; top: 0; bottom: 0; width: 3px;
    background: var(--gold);
  }
  .holder {
    position: absolute; left: 72px; top: 34px;
  }
  .holder .name {
    font-family: "Cinzel", serif; font-weight: 700; font-size: 19px;
    letter-spacing: 1px; color: var(--ink);
  }
  .holder .role {
    font-family: "Libre Baskerville", serif; font-size: 10px; color: var(--ink-soft);
    margin-top: 2px;
  }
  .contact {
    position: absolute; left: 72px; top: 168px; list-style: none;
    font-family: "Libre Baskerville", serif; font-size: 11.5px; color: var(--ink);
    line-height: 17px;
  }
  .contact li { display: flex; align-items: center; gap: 8px; white-space: nowrap; }
  .contact .icon { width: 11px; height: 11px; flex: none; }
  .contact .no-icon { width: 11px; flex: none; }
  .brand {
    position: absolute; right: 30px; top: 108px;
    display: flex; align-items: center; gap: 10px;
  }
  .brand .brand-mark { width: 16px; height: 16px; background: var(--gold); }
  .brand .brand-name {
    font-family: "Cinzel", serif; font-weight: 700; font-size: 21px;
    letter-spacing: 1px; color: var(--ink); white-space: nowrap;
  }
</style>
</head>
<body>
<main class="canvas">
  <section class="card card-back" aria-label="Card back">
    <span class="brand-mark"></span>
    <span class="brand-name">Harcourt Memorials</span>
  </section>

  <section class="card card-front" aria-label="Card front">
    <div class="stripe"></div>
    <div class="gold-rule"></div>

    <div class="holder">
      <h1 class="name">Simon Harcourt</h1>
      <p class="role">Operations Manager</p>
    </div>

    <div class="brand">
      <span class="brand-mark"></span>
      <span class="brand-name">Harcourt Memorials</span>
    </div>

    <ul class="contact">
      <li>
        <svg class="icon" viewBox="0 0 12 12"><rect x="3" y="0.5" width="6" height="11" rx="1.2" fill="var(--gold)"/><rect x="4" y="2" width="4" height="7" fill="var(--card-white)"/></svg>
        0417293086
      </li>
      <li>
        <svg class="icon" viewBox="0 0 12 12"><path d="M2 3c0-1 1-2 2-2l1 2-1 1.5c.6 1.4 1.6 2.4 3 3L8.5 6l2 1c0 1-1 2-2 2C5 9 2 6 2 3z" fill="var(--gold)"/></svg>
        02 9561 3048
      </li>
      <li>
        <svg class="icon" viewBox="0 0 12 12"><rect x="0.5" y="2.5" width="11" height="7" fill="var(--gold)"/><path d="M0.5 2.5 6 7l5.5-4.5" fill="none" stroke="var(--card-white)" stroke-width="1"/></svg>
        simon@harcourtmemorials.com.au
      </li>
      <li>
        <svg class="icon" viewBox="0 0 12 12"><circle cx="6" cy="6" r="5.5" fill="var(--gold)"/><path d="M0.5 6h11M6 0.5c-2.5 3-2.5 8 0 11M6 0.5c2.5 3 2.5 8 0 11" fill="none" stroke="var(--card-white)" stroke-width="0.8"/></svg>
        www.harcourtmemorials.com.au
      </li>
      <li><span class="no-icon"></span>Suite 17, 8 Palfrey Lane, West Carlow, Sydney NSW 2156</li>
    </ul>
  </section>
</main>
</body>
</html>
```